A website for a Maltese Law Firm

Our law firm needs a website to further its business. The site should have a simple yet effective design. We would need the following sections: About us, Practice Areas, About Malta, Contact. These should be further split as follows:

About us: Our firm, Our values, What others say, Offices

Practice Areas: Crimimal, Citizenship & Residence, Sovereign Patron Pathway, Criminal Defence, Civil Litigation, Arbitration and ADR, Commercial and Corporate, Media Law.

About Malta: just one section.

Contact: Just one section

We would also need a news feed at the front of the site to include latest news regarding our cases.

At the bottom we need a section for our Terms and a Privacy Statement.

Our logo is being attached.

Target Market(s)

All clients looking for legal assistance in Malta

Industry/Entity Type

Legal

Coding

Coded - Design and coding required

Number of Pages Required

1 page

Requirements
Must have
• It must be simple yet striking.

```html
<!DOCTYPE html>
<html lang="en">
<head>
<meta charset="utf-8">
<title>Falzon &amp; Grech Advocates</title>
<link rel="stylesheet" href="https://fonts.googleapis.com/css2?family=Cinzel:wght@400;700&family=Open+Sans:ital,wght@0,400;0,600;0,700;1,400;1,700&family=Roboto+Condensed:wght@400&display=swap">
<style>
:root{
  --ink:#111;
  --text:#333;
  --muted:#555;
  --topbar:#5a5a5a;
  --white:#fff;
  --light:#efefef;
  --footer:#e4e4e4;
  --rule:#bdbdbd;
  --sky-top:#3f7fd0;
  --sky-low:#a9c9ea;
  --stone:#c9a36c;
  --sea:#1d5f8c;
}
*{box-sizing:border-box;margin:0;padding:0}
html,body{width:1200px;height:2413px;overflow:hidden;background:var(--white)}
body{position:relative;font-family:"Open Sans",Arial,sans-serif;color:var(--text)}
.abs{position:absolute}
.serif{font-family:"Cinzel",Georgia,serif}

/* top bar */
.topbar{left:0;top:0;width:1200px;height:35px;background:var(--topbar)}
.social{display:flex;gap:8px;position:absolute;left:80px;top:8px}
.social span{width:19px;height:19px;background:var(--white);display:block}
.top-contact{position:absolute;right:80px;top:0;height:35px;display:flex;align-items:center;gap:14px;color:var(--white);font-size:13px}
.top-contact .ico{width:22px;height:22px;background:var(--white);display:inline-flex;align-items:center;justify-content:center;margin-right:8px;vertical-align:middle}

/* header */
.wordmark{font-family:"Cinzel",Georgia,serif;font-weight:400;color:var(--ink);white-space:nowrap}
.logo{left:80px;top:84px;font-size:22px;line-height:28px}
.cta{left:843px;top:43px;width:278px;height:37px;background:var(--ink);color:var(--white);font-family:"Cinzel",Georgia,serif;font-size:16px;display:flex;align-items:center;justify-content:center}
.nav{left:405px;top:100px;display:flex;font-family:"Cinzel",Georgia,serif;font-size:13.5px;color:var(--muted)}
.nav a{color:inherit;text-decoration:none;padding:0 9px;border-left:1px solid #aaa;line-height:18px}
.nav a:first-child{border-left:0;padding-left:0;color:var(--ink);font-weight:700}

/* hero */
.hero{left:0;top:143px;width:1200px;height:510px;background:linear-gradient(180deg,var(--sky-top) 0%,var(--sky-low) 45%,var(--stone) 62%,var(--sea) 82%,#0f3e66 100%)}
.hero-caption{left:85px;top:327px;width:549px;height:143px;background:rgba(20,30,45,.78);color:var(--white);padding:12px 13px}
.hero-caption h1{font-family:"Cinzel",Georgia,serif;font-weight:400;font-size:24px;line-height:30px;white-space:nowrap}
.hero-caption p{font-size:12px;line-height:18px;margin-top:6px}
.hero-caption .btn{display:inline-block;margin-top:10px;background:#ddd;color:var(--ink);font-size:13px;font-weight:700;padding:6px 18px}
.hero-arrow{width:30px;height:30px;border-radius:50%;display:flex;align-items:center;justify-content:center}

/* about */
.about-title{left:0;top:704px;width:1200px;text-align:center;font-family:"Cinzel",Georgia,serif;font-size:28px;color:var(--ink)}
.about-copy{left:90px;top:758px;width:1020px;font-size:11.6px;line-height:19px;text-align:center}
.about-copy p+p{margin-top:10px}
.btn-dark{background:var(--ink);color:var(--white);font-size:13px;font-weight:700;display:flex;align-items:center;justify-content:center}

/* practice */
.practice{left:0;top:959px;width:1200px;height:397px;background:linear-gradient(180deg,#3b3836,#262322 60%,#1e1b1a)}
.practice-title{left:80px;top:976px;width:677px;font-family:"Cinzel",Georgia,serif;font-size:28px;color:var(--white);border-bottom:1px solid #666;padding-bottom:6px}
.area{display:flex;align-items:center;gap:14px;color:var(--white);font-family:Georgia,"Times New Roman",serif;font-size:17px}
.area .icon{width:40px;height:40px;border:1px solid #ddd;display:flex;align-items:center;justify-content:center}
.call{left:80px;top:1284px;color:var(--white);font-family:"Roboto Condensed",Arial,sans-serif;font-size:22px}
.quote-form{left:814px;top:981px;width:302px;height:325px;background:rgba(90,90,90,.55);padding:6px 12px}
.quote-form h3{font-family:"Cinzel",Georgia,serif;font-weight:400;font-size:19px;line-height:22px;color:var(--white)}
.field{background:rgba(185,185,185,.55);color:var(--white);font-size:12px;height:37px;margin-top:8px;padding:10px 10px;position:relative}
.field.msg{height:64px}
.submit{width:103px;height:30px;background:var(--ink);color:var(--white);font-size:13px;font-weight:700;display:flex;align-items:center;justify-content:center;margin-top:14px}

/* testimonials */
.testimonials{left:0;top:1356px;width:1200px;height:357px;background:var(--light)}
.section-title{font-family:"Cinzel",Georgia,serif;font-size:28px;color:var(--ink)}
.avatar{left:124px;top:1480px;width:106px;height:106px;border-radius:50%;background:linear-gradient(160deg,#d8c4ae,#9aa7b4);border:3px solid var(--white)}
.quote{left:270px;top:1482px;width:810px;font-size:12px;line-height:22.5px;font-style:italic}
.author{left:270px;top:1607px;font-size:11.5px;font-style:italic;font-weight:700;color:var(--ink)}
.pager{display:flex;gap:8px}
.pager span{width:22px;height:20px;border:1.5px solid var(--ink);display:flex;align-items:center;justify-content:center;background:var(--white)}

/* case study */
.case-title{left:80px;top:1762px;border-bottom:1px solid var(--rule);padding-bottom:4px}
.case-img{width:216px;height:216px}
.case-text{width:300px}
.case-text h4{font-size:14.5px;line-height:21px;color:var(--ink);font-weight:700}
.case-text p{font-size:12.5px;line-height:19px;margin-top:12px;color:#444}
.case-text .date{font-style:italic;font-size:12.5px;margin-top:12px;color:#555}
.case-text .btn-dark{width:80px;height:30px;margin-top:12px}

/* footer */
.footer{left:0;top:2112px;width:1200px;height:274px;background:var(--footer)}
.follow{left:88px;top:2099px;width:211px;height:37px;background:var(--ink);color:var(--white);font-size:12px;display:flex;align-items:center;gap:8px;padding-left:16px}
.follow span{width:20px;height:20px;border:1px solid var(--white);display:block}
.foot-h{font-family:"Cinzel",Georgia,serif;font-size:15px;color:var(--ink);border-bottom:1px solid var(--rule);padding-bottom:6px}
.links{list-style:none;font-size:12px;line-height:22px;margin-top:10px}
.links li::before{content:"›";margin-right:10px;color:#777}
.contacts{font-size:12px;line-height:17px;margin-top:12px}
.contacts div{display:flex;gap:10px;margin-bottom:10px}
.contacts .ico{width:16px;height:16px;background:var(--ink);flex:none;display:flex;align-items:center;justify-content:center}
.map{left:587px;top:2172px;width:262px;height:170px;background:linear-gradient(135deg,#c9d9b9,#e7e3d6 55%,#a9c8e4);border:2px solid #999}
.foot-mark{font-size:15px;line-height:20px;color:#444}
.hours{font-size:11.5px;line-height:18px}
.hours .row{display:flex;justify-content:space-between;border-bottom:1px solid var(--rule);padding:8px 0;font-size:11.5px}
.copyright{left:0;top:2386px;width:1200px;height:16px;font-size:11px;text-align:center;color:var(--text);background:var(--footer)}
.bottom-strip{left:0;top:2402px;width:1200px;height:11px;background:var(--ink)}
</style>
</head>
<body>

<!-- top bar -->
<div class="abs topbar">
  <div class="social"><span></span><span></span><span></span><span></span></div>
  <div class="top-contact">
    <span><span class="ico"><svg width="14" height="14" viewBox="0 0 24 24"><path d="M6.6 10.8a15 15 0 0 0 6.6 6.6l2.2-2.2c.3-.3.7-.4 1-.2 1.1.4 2.3.6 3.6.6.6 0 1 .4 1 1V20c0 .6-.4 1-1 1A17 17 0 0 1 3 4c0-.6.4-1 1-1h3.5c.6 0 1 .4 1 1 0 1.3.2 2.5.6 3.6.1.3 0 .7-.2 1z" fill="#5a5a5a"/></svg></span>356 2000 1100</span>
    <span><span class="ico"><svg width="14" height="12" viewBox="0 0 24 18"><rect x="1" y="1" width="22" height="16" fill="#5a5a5a"/><path d="M1 1l11 9 11-9" stroke="#fff" stroke-width="2" fill="none"/></svg></span>mark@fgadvocates.com</span>
  </div>
</div>

<!-- header -->
<div class="abs wordmark logo">Falzon &amp; Grech Advocates</div>
<div class="abs cta">Schedule Free Consultation</div>
<nav class="abs nav">
  <a>Home</a><a>About Us</a><a>Our Firm</a><a>Our Values</a><a>What Others Say</a><a>Offices</a><a>Contact Us</a>
</nav>

<!-- hero -->
<div class="abs hero" role="img" aria-label="Photograph of the Valletta harbour skyline with a domed church under a blue sky"></div>
<div class="abs hero-caption">
  <h1>Get Qualified Legal Advice In Malta</h1>
  <p>Lorem ipsum dolor sit amet, consectetuer adipiscing elit, sed diam nonummy nibh euismod tincidunt ut laoreet dolore magna aliquam erat volutpat.</p>
  <span class="btn">Read More</span>
</div>
<div class="abs hero-arrow" style="left:35px;top:383px;background:var(--white)"><svg width="10" height="12" viewBox="0 0 10 12"><path d="M7 1L2 6l5 5" stroke="#111" stroke-width="2" fill="none"/></svg></div>
<div class="abs hero-arrow" style="left:1134px;top:383px;background:var(--ink)"><svg width="10" height="12" viewBox="0 0 10 12"><path d="M3 1l5 5-5 5" stroke="#fff" stroke-width="2" fill="none"/></svg></div>

<!-- about -->
<div class="abs about-title">About Falzon &amp; Grech Advocates</div>
<div class="abs about-copy">
  <p>Lorem ipsum dolor sit amet, consectetuer adipiscing elit, sed diam nonummy nibh euismod tincidunt ut laoreet dolore magna aliquam erat volutpat. Ut wisi enim ad minim veniam, quis nostrud exerci tation ullamcorper suscipit lobortis nisl ut aliquip ex ea commodo consequat. Duis autem vel eum iriure dolor in hendrerit in vulputate velit esse molestie consequat, vel illum dolore eu feugiat nulla facilisis at vero eros et accumsan et iusto odio dignissim qui blandit praesent luptatum zzril delenit augue duis dolore te feugait nulla facilisi.</p>
  <p>Lorem ipsum dolor sit amet, consectetuer adipiscing elit, sed diam nonummy nibh euismod tincidunt ut laoreet dolore magna aliquam erat volutpat. Ut wisi enim ad minim veniam, quis nostrud exerci tation ullamcorper suscipit lobortis nisl ut aliquip ex ea commodo consequat. Duis autem vel eum iriure dolor in hendrerit in vulputate velit esse molestie consequat,</p>
</div>
<div class="abs btn-dark" style="left:549px;top:890px;width:102px;height:28px">Read More</div>

<!-- practice areas -->
<div class="abs practice" role="img" aria-label="Darkened photograph of Valletta rooftops and a church dome"></div>
<div class="abs practice-title">Our Practice Areas</div>
<div class="abs area" style="left:80px;top:1046px"><span class="icon"><svg width="24" height="24" viewBox="0 0 24 24" fill="none" stroke="#fff" stroke-width="1.6"><circle cx="9" cy="6" r="3"/><path d="M4 21v-6a5 5 0 0 1 10 0v6M15 12l6 6"/></svg></span>Criminal Law</div>
<div class="abs area" style="left:80px;top:1106px"><span class="icon"><svg width="24" height="24" viewBox="0 0 24 24" fill="none" stroke="#fff" stroke-width="1.6"><circle cx="12" cy="5" r="3"/><path d="M7 21l2-9h6l2 9M12 12v9"/></svg></span>Citizenship &amp; Residence</div>
<div class="abs area" style="left:80px;top:1165px"><span class="icon"><svg width="24" height="24" viewBox="0 0 24 24" fill="none" stroke="#fff" stroke-width="1.6"><circle cx="8" cy="5" r="2.5"/><path d="M8 8v8M4 21l4-5 4 5M13 10h8v8h-8z"/></svg></span>Sovereign Patron Pathway</div>
<div class="abs area" style="left:80px;top:1223px"><span class="icon"><svg width="24" height="24" viewBox="0 0 24 24" fill="none" stroke="#fff" stroke-width="1.6"><path d="M3 21h18M5 21V10h5v11M12 21V4h7v17M14 7h3M14 11h3M14 15h3"/></svg></span>Commercial &amp; Corporate</div>
<div class="abs area" style="left:468px;top:1046px"><span class="icon"><svg width="24" height="24" viewBox="0 0 24 24" fill="none" stroke="#fff" stroke-width="1.6"><circle cx="7" cy="15" r="4.5"/><circle cx="17" cy="15" r="4.5"/><path d="M9 11l3-6 3 6"/></svg></span>Criminal Defence</div>
<div class="abs area" style="left:468px;top:1106px"><span class="icon"><svg width="24" height="24" viewBox="0 0 24 24" fill="none" stroke="#fff" stroke-width="1.6"><path d="M4 10l6-6 4 4-6 6zM10 10l10 10M3 21h9"/></svg></span>Civil Litigation</div>
<div class="abs area" style="left:468px;top:1165px"><span class="icon"><svg width="24" height="24" viewBox="0 0 24 24" fill="none" stroke="#fff" stroke-width="1.6"><circle cx="6" cy="7" r="2"/><circle cx="12" cy="5" r="2"/><circle cx="18" cy="7" r="2"/><path d="M3 20v-6h18v6M6 10v4M12 8v6M18 10v4"/></svg></span>Arbitration &amp; ADR</div>
<div class="abs area" style="left:468px;top:1223px"><span class="icon"><svg width="24" height="24" viewBox="0 0 24 24" fill="none" stroke="#fff" stroke-width="1.6"><path d="M12 3v17M7 20h10M4 7h16M4 7l-3 7h6zM20 7l-3 7h6z"/></svg></span>Media Law</div>
<div class="abs call">Call us 356 2000 1100&nbsp; at&nbsp; or&nbsp; contact us online for a Free estimate</div>

<div class="abs quote-form">
  <h3>Request for Free Consulatation</h3>
  <div class="field" style="margin-top:14px">Name</div>
  <div class="field">Email</div>
  <div class="field">Inquiry Tpye<span style="position:absolute;right:14px;top:10px">v</span></div>
  <div class="field msg">Message</div>
  <div class="submit">SUBMIT</div>
</div>

<!-- testimonials -->
<div class="abs testimonials"></div>
<div class="abs section-title" style="left:0;top:1414px;width:1200px;text-align:center">What Other's Say About Us</div>
<div class="abs" style="left:470px;top:1458px;width:260px;height:1px;background:var(--rule)"></div>
<div class="abs avatar" role="img" aria-label="Portrait photograph of a client"></div>
<div class="abs" style="left:268px;top:1480px;font-size:34px;color:#aaa;font-family:Georgia,serif;line-height:20px">&ldquo;</div>
<div class="abs quote">&emsp;&emsp;Lorem ipsum dolor sit amet, consectetuer adipiscing elit, sed diam nonummy nibh euismod tincidunt ut laoreet dolore magna aliquam erat volutpat. Ut wisi enim ad minim veniam, quis nostrud exerci tation ullamcorper suscipit lobortis nisl ut aliquip commodo consequat. Duis autem vel eum iriure dolor in hendrerit in vulputate velit esse molestie consequat, vel illum dolore eu feugiat nulla facilisis at vero eros et accumsan et iusto odio dignissimaugue duis dolore te feugait nulla facilisi.</div>
<div class="abs author">.... Lorem Ispum, Manger</div>
<div class="abs pager" style="left:574px;top:1640px"><span><svg width="8" height="10" viewBox="0 0 8 10"><path d="M6 1L2 5l4 4" stroke="#111" stroke-width="1.6" fill="none"/></svg></span><span><svg width="8" height="10" viewBox="0 0 8 10"><path d="M2 1l4 4-4 4" stroke="#111" stroke-width="1.6" fill="none"/></svg></span></div>

<!-- case study -->
<div class="abs section-title case-title">Case Study</div>
<div class="abs pager" style="left:1066px;top:1773px"><span><svg width="8" height="10" viewBox="0 0 8 10"><path d="M6 1L2 5l4 4" stroke="#111" stroke-width="1.6" fill="none"/></svg></span><span><svg width="8" height="10" viewBox="0 0 8 10"><path d="M2 1l4 4-4 4" stroke="#111" stroke-width="1.6" fill="none"/></svg></span></div>

<div class="abs case-img" style="left:80px;top:1829px;background:linear-gradient(160deg,#5a3a22,#a0784e 60%,#6b4a2c)" role="img" aria-label="Photograph of two lawyers reviewing documents at a wooden desk"></div>
<div class="abs case-text" style="left:317px;top:1827px">
  <h4>Ut wisi enim ad minim veniam<br>quis nostrud exerci tation</h4>
  <p>Lorem ipsum dolor sit amet, consectetuer adipiscing elit, sed diam nonummy nibh euismod tincidunt ut laoreet dolore magna aliquam erat volutpat.</p>
  <div class="date">2014-11-26-23:14:43</div>
  <div class="btn-dark">Read More</div>
</div>
<div class="abs" style="left:317px;top:1880px;width:245px;height:1px;background:var(--rule)"></div>

<div class="abs case-img" style="left:621px;top:1829px;background:linear-gradient(160deg,#c9b79c,#e8ddd0 55%,#4a4a4a)" role="img" aria-label="Photograph of a lawyer writing beside a statue of justice holding scales"></div>
<div class="abs case-text" style="left:861px;top:1827px">
  <h4>Ut wisi enim ad minim veniam<br>quis nostrud exerci tation</h4>
  <p>Lorem ipsum dolor sit amet, consectetuer adipiscing elit, sed diam nonummy nibh euismod tincidunt ut laoreet dolore magna aliquam erat volutpat.</p>
  <div class="date">2014-11-26-23:14:43</div>
  <div class="btn-dark">Read More</div>
</div>
<div class="abs" style="left:861px;top:1880px;width:257px;height:1px;background:var(--rule)"></div>

<!-- footer -->
<div class="abs footer"></div>
<div class="abs follow">Follow us<span style="margin-left:8px"></span><span></span><span></span><span></span></div>

<div class="abs" style="left:85px;top:2167px;width:175px">
  <div class="foot-h">Quick Links</div>
  <ul class="links"><li>Home</li><li>About Us</li><li>Our Firm</li><li>Our Values</li><li>What Others Say</li><li>Offices</li><li>Contact Us</li></ul>
</div>

<div class="abs" style="left:310px;top:2167px;width:195px">
  <div class="foot-h">Contact Details</div>
  <div class="contacts">
    <div><span class="ico"><svg width="10" height="12" viewBox="0 0 10 12"><path d="M5 11S1 6.5 1 4a4 4 0 0 1 8 0c0 2.5-4 7-4 7z" fill="#fff"/></svg></span><span>12/4, Merchant Lane, Valletta<br>218, Olive Street, Birkirkara</span></div>
    <div><span class="ico"><svg width="10" height="10" viewBox="0 0 24 24"><path d="M6.6 10.8a15 15 0 0 0 6.6 6.6l2.2-2.2c.3-.3.7-.4 1-.2 1.1.4 2.3.6 3.6.6.6 0 1 .4 1 1V20c0 .6-.4 1-1 1A17 17 0 0 1 3 4c0-.6.4-1 1-1h3.5c.6 0 1 .4 1 1 0 1.3.2 2.5.6 3.6.1.3 0 .7-.2 1z" fill="#fff"/></svg></span>356 2000 1100 ( Valletta )</div>
    <div><span class="ico"><svg width="10" height="10" viewBox="0 0 24 24"><path d="M6.6 10.8a15 15 0 0 0 6.6 6.6l2.2-2.2c.3-.3.7-.4 1-.2 1.1.4 2.3.6 3.6.6.6 0 1 .4 1 1V20c0 .6-.4 1-1 1A17 17 0 0 1 3 4c0-.6.4-1 1-1h3.5c.6 0 1 .4 1 1 0 1.3.2 2.5.6 3.6.1.3 0 .7-.2 1z" fill="#fff"/></svg></span>356 2000 1188 (Birkirkara )</div>
    <div><span class="ico"><svg width="10" height="8" viewBox="0 0 24 18"><path d="M1 1l11 9 11-9" stroke="#fff" stroke-width="3" fill="none"/></svg></span>mark@fgadvocates.com</div>
  </div>
</div>

<div class="abs map" role="img" aria-label="Map of Malta showing Valletta and Birkirkara office locations"></div>

<div class="abs" style="left:893px;top:2130px;width:225px">
  <div class="wordmark foot-mark">Falzon &amp; Grech Advocates</div>
  <div class="foot-h" style="margin-top:14px">Meeting Hours</div>
  <div class="hours">
    <p style="margin-top:10px;border-bottom:1px solid var(--rule);padding-bottom:8px">Lorem ipsum is the dummy text of the industry&nbsp; lorem fds fdurei.</p>
    <div class="row"><span>Monday-Friday:</span><span>9am to 5pm</span></div>
    <div class="row"><span>Saturday:</span><span>10am to 2pm</span></div>
    <div class="row" style="border-bottom:0"><span>Sunday:</span><span>Clised</span></div>
  </div>
</div>

<div class="abs copyright"><span style="display:inline-block;width:170px;height:1px;background:#999;vertical-align:middle;margin-right:14px"></span>Copyright &copy; 2016 Falzon &amp; Grech Advocates. All Rights Reserved.&nbsp; Disclaimer<span style="display:inline-block;width:170px;height:1px;background:#999;vertical-align:middle;margin-left:14px"></span></div>
<div class="abs bottom-strip"></div>

</body>
</html>
```